Redesign of business card for Cedar Ridge Mechanical

We are looking for a new design for our business cards for Cedar Ridge Mechanical. We are a plumbing & HVAC construction company, operating on the West Coast of Canada and USA. Logo attached.
Industry/Entity Type
Construction - Plumbing & HVAC
Contact Information for Business Card
Name, address, phone numbers, email, website address
Look and feel
Each slider illustrates characteristics of the customer's brand and the style your logo design should communicate.

```html
<!DOCTYPE html>
<html lang="en">
<head>
<meta charset="utf-8">
<title>Cedar Ridge Mechanical – Business Card</title>
<link href="https://fonts.googleapis.com/css2?family=Montserrat:wght@400;500;700&display=swap" rel="stylesheet">
<style>
  :root {
    --ink: #0b0b0b;
    --paper: #ffffff;
    --backdrop: #c9c9c9;
    --muted: #333333;
  }
  * { box-sizing: border-box; margin: 0; padding: 0; }
  html, body { width: 1200px; height: 896px; overflow: hidden; }
  body {
    background: var(--backdrop);
    font-family: "Montserrat", Arial, sans-serif;
    color: var(--ink);
    position: relative;
  }
  .card {
    position: absolute;
    left: 336px;
    width: 527px;
    height: 300px;
    background: var(--paper);
    border-radius: 26px;
    overflow: hidden;
  }
  .card--front { top: 126px; }
  .card--back { top: 475px; }

  .brand { display: flex; align-items: center; gap: 10px; font-weight: 700; text-transform: uppercase; color: var(--ink); }
  .brand__square { background: var(--ink); flex: none; }

  .card--front .brand {
    position: absolute; left: 0; right: 0; top: 0; bottom: 0;
    justify-content: center; font-size: 26px; letter-spacing: 1px; gap: 14px;
  }
  .card--front .brand__square { width: 30px; height: 30px; }

  .card--back .brand { position: absolute; left: 21px; top: 40px; font-size: 14px; letter-spacing: .5px; gap: 8px; }
  .card--back .brand__square { width: 16px; height: 16px; }

  .person { position: absolute; right: 16px; top: 22px; text-align: right; }
  .person__name { font-weight: 700; font-size: 20px; letter-spacing: .5px; }
  .person__role { font-size: 12.5px; color: var(--muted); margin-top: 4px; }
  .person__bar { position: absolute; right: 0; top: 26px; width: 5px; height: 38px; background: var(--ink); }

  .address { position: absolute; left: 21px; top: 162px; font-size: 14.5px; line-height: 21px; color: #222; }

  .contact-band {
    position: absolute; left: 0; right: 0; top: 223px; bottom: 0;
    background: var(--ink);
  }
  .contact-list { position: absolute; left: 21px; top: 224px; list-style: none; color: var(--paper); font-size: 14.5px; }
  .contact-list li { display: flex; align-items: center; gap: 8px; height: 21px; }
  .contact-list svg { width: 11px; height: 11px; fill: var(--paper); flex: none; }

  .brand-tab {
    position: absolute; left: 380px; top: 205px; width: 147px; height: 78px;
    background: var(--paper); border-radius: 0 0 0 16px;
    display: flex; align-items: center; justify-content: center;
  }
  .brand-tab .brand { position: static; font-size: 10px; gap: 6px; }
  .brand-tab .brand__square { width: 12px; height: 12px; }
</style>
</head>
<body>
  <section class="card card--front">
    <div class="brand"><span class="brand__square"></span>Cedar Ridge Mechanical</div>
  </section>

  <section class="card card--back">
    <div class="brand"><span class="brand__square"></span>Cedar Ridge Mechanical</div>

    <div class="person">
      <p class="person__name">DANIEL WHITFORD</p>
      <p class="person__role">Managing Director</p>
    </div>
    <span class="person__bar"></span>

    <p class="address">Your address, City<br>State, Zip 1234</p>

    <div class="contact-band"></div>
    <ul class="contact-list">
      <li><svg viewBox="0 0 24 24"><path d="M6.6 10.8a15 15 0 0 0 6.6 6.6l2.2-2.2a1 1 0 0 1 1-.25 11.4 11.4 0 0 0 3.6.57 1 1 0 0 1 1 1V20a1 1 0 0 1-1 1A17 17 0 0 1 3 4a1 1 0 0 1 1-1h3.5a1 1 0 0 1 1 1c0 1.25.2 2.45.57 3.57a1 1 0 0 1-.25 1z"/></svg>123 456 789</li>
      <li><svg viewBox="0 0 24 24"><path d="M2 5h20v14H2z M4 7v.5l8 5 8-5V7l-8 5z"/></svg>info@yourgmail.com</li>
      <li><svg viewBox="0 0 24 24"><path d="M12 2a10 10 0 1 0 0 20 10 10 0 0 0 0-20zm6.9 6h-3a15 15 0 0 0-1.3-4A8 8 0 0 1 18.9 8zM12 4a13 13 0 0 1 1.9 4h-3.8A13 13 0 0 1 12 4zM4.3 14a8 8 0 0 1 0-4h3.4a16 16 0 0 0 0 4zm.8 2h3a15 15 0 0 0 1.3 4A8 8 0 0 1 5.1 16zm3-8h-3a8 8 0 0 1 4.3-4 15 15 0 0 0-1.3 4zM12 20a13 13 0 0 1-1.9-4h3.8A13 13 0 0 1 12 20zm2.3-6H9.7a14 14 0 0 1 0-4h4.6a14 14 0 0 1 0 4zm.3 6a15 15 0 0 0 1.3-4h3a8 8 0 0 1-4.3 4zm1.7-6a16 16 0 0 0 0-4h3.4a8 8 0 0 1 0 4z"/></svg>www.yourwebsite.com</li>
    </ul>

    <div class="brand-tab">
      <div class="brand"><span class="brand__square"></span>Cedar Ridge</div>
    </div>
  </section>
</body>
</html>
```